Start up Dialysis Clinic needs its first website - Velmira Health

Create a visually appealing and user-friendly website for Velmira Health, a dialysis clinic located in Mt. Irvine, Tobago. The website should effectively communicate our services to local, regional, and international patients, providing essential information and fostering trust and engagement..
Key Goals:

1. Informative: Provide comprehensive information about our services, facility, and team.
2. User-Friendly: Ensure the website is easy to navigate, with a clear structure and accessible content.
3. Engaging: Create a visually appealing design that reflects the professionalism and care of Velmira Health.
4. Responsive: Ensure the website is fully responsive and performs well on all devices, including desktops, tablets, and smartphones.
5. Trust-Building: Include testimonials, credentials, and patient resources to build trust with potential patients.
Scope of Work:

1. Home Page: An inviting and informative landing page that provides an overview of our clinic, mission, and services. Include a call to action for more information and contact details.
2. About Us: A detailed page about Velmira Health, including our mission, vision, team, and facility tour.
3. Services: A comprehensive page describing the dialysis services we offer, including Hemodialysis, Peritoneal Dialysis, and Home Hemodialysis.
4. Patient Information: A resourceful section with guides for new patients, FAQs, insurance and billing information, and downloadable forms.
5. Resources: Educational content about kidney health, dialysis options, diet and nutrition tips, and support groups.
6. Contact Us: A contact page with our address, phone number, email, office hours, a contact form, and a map.

```html
<!DOCTYPE html>
<html lang="en">
<head>
<meta charset="utf-8">
<title>Velmira Health — Dialysis Clinic</title>
<link href="https://fonts.googleapis.com/css2?family=Outfit:wght@300;400;500;600&family=Roboto:wght@400;500;700&display=swap" rel="stylesheet">
<style>
:root{
  --blue:#3f78c0;
  --blue-deep:#2f62a8;
  --green:#6aa23b;
  --text:#4a4a4a;
  --muted:#6b6b6b;
  --white:#ffffff;
  --soft:#f4f7fb;
}
*{box-sizing:border-box;margin:0;padding:0}
html,body{width:1200px;height:3855px;overflow:hidden;background:var(--white)}
body{font-family:"Outfit",sans-serif;color:var(--text)}
.page{position:relative;width:1200px;height:3855px;overflow:hidden}
.abs{position:absolute}
.heading{font-family:"Roboto",sans-serif;font-weight:500;color:var(--blue);letter-spacing:.5px}
.eyebrow{font-family:"Roboto",sans-serif;font-weight:500;color:var(--green);font-size:16px;letter-spacing:.5px}
.rule{display:flex;gap:4px;align-items:center}
.rule span{display:block;height:3px;background:var(--blue);width:46px;border-radius:2px}
.rule span+span{width:10px;background:var(--green)}
.center{left:0;width:1200px;text-align:center}
.center .rule{justify-content:center}

/* header */
.topline{left:0;top:0;width:1200px;height:4px;background:var(--green)}
.contact-pill{left:571px;top:0;width:484px;height:42px;display:flex;font-size:12px;font-weight:500;color:var(--white)}
.contact-pill .call{flex:0 0 210px;background:var(--green);border-radius:0 0 0 22px;display:flex;align-items:center;justify-content:center;gap:6px}
.contact-pill .mail{flex:1;background:var(--blue);border-radius:0 0 22px 22px;display:flex;align-items:center;justify-content:center;gap:6px;margin-left:-12px}
.brand{font-family:"Outfit",sans-serif;font-weight:600;color:var(--blue);line-height:1;text-align:center}
.header-brand{left:140px;top:30px;width:120px;font-size:22px}
.header-brand small{display:block;font-size:13px;letter-spacing:3px;margin-top:4px;font-weight:600}
.nav{left:388px;top:70px;display:flex;align-items:center;font-size:12px;color:#222}
.nav a{color:inherit;text-decoration:none}
.nav .dot{width:3px;height:3px;border-radius:50%;background:#999;margin:6px 20px 0}
.nav .active{color:var(--green)}
.quote-btn{left:932px;top:60px;width:123px;height:39px;border:2px solid var(--blue);border-radius:22px;color:var(--blue);font-size:12px;display:flex;align-items:center;justify-content:center}

/* hero */
.hero-photo{left:0;top:112px;width:1200px;height:600px;background:linear-gradient(100deg,#f3f5f8 0%,#e9edf2 30%,#cfd9e2 55%,#9fb9c9 75%,#c9d4dd 100%)}
.hero-title{left:181px;top:270px;font-family:"Roboto",sans-serif;font-weight:700;font-size:68px;line-height:70px;color:var(--blue);letter-spacing:1px}
.outline-btn{border:2px solid var(--blue);border-radius:22px;color:var(--blue);font-size:12px;display:flex;align-items:center;justify-content:center;gap:5px;font-weight:500;background:rgba(255,255,255,.6)}
.hero-btn{left:181px;top:422px;width:139px;height:39px}
.follow-line{left:70px;top:215px;width:1px;height:150px;background:#bbb}
.social{left:56px;width:30px;height:30px;border:1.5px solid var(--blue);border-radius:50%;display:flex;align-items:center;justify-content:center}
.follow-text{left:52px;top:545px;font-size:10px;color:#888;transform:rotate(-90deg);transform-origin:left top;letter-spacing:1px}
.dots{left:184px;top:563px;display:flex;gap:4px}
.dots span{width:28px;height:4px;border-radius:2px;background:#9fb7d8}
.dots span.on{background:var(--green)}

/* about */
.about-leaf{left:117px;top:808px;width:238px;height:230px;border-radius:0 140px 0 140px;background:linear-gradient(135deg,#6aa23b,#4e8a2a)}
.about-ring{left:156px;top:868px;width:398px;height:398px;border-radius:50%;background:var(--blue)}
.about-photo{left:189px;top:901px;width:332px;height:332px;border-radius:50%;border:4px solid var(--white);background:linear-gradient(160deg,#eef1f4,#c9cfd6 55%,#8f8174)}
.about-text{left:598px;top:820px;width:454px}
.about-text .heading{font-size:34px;margin:8px 0 14px}
.about-text p{font-size:12.4px;line-height:20.8px;text-align:justify;color:var(--muted);margin-top:22px}
.learn-btn{position:relative;width:138px;height:38px;margin-top:22px}

/* mission */
.mission-band{left:0;top:1324px;width:1200px;height:420px}
.mission-text{left:157px;top:1432px;width:456px;color:var(--white)}
.mission-text h2{font-family:"Roboto",sans-serif;font-weight:500;font-size:36px;letter-spacing:.5px;margin-bottom:14px}
.mission-text .rule span{background:var(--white)}
.mission-text p{font-size:12.6px;line-height:20.6px;margin-top:20px;text-align:justify}
.mission-photo{left:690px;top:1340px;width:510px;height:400px;background:linear-gradient(90deg,rgba(79,136,120,0),rgba(120,160,80,.55) 40%,rgba(106,162,59,.35));border-radius:0 0 0 0}

/* services */
.services-head{top:1808px}
.services-head .heading{font-size:38px;margin:6px 0 12px}
.service{top:1922px;width:280px}
.service .photo{height:314px;border-radius:14px}
.service .label{margin-top:8px;height:64px;border-radius:18px;background:var(--blue);color:var(--white);font-family:"Roboto",sans-serif;font-weight:500;font-size:20px;display:flex;align-items:center;justify-content:center;letter-spacing:.5px}
.service .label.alt{background:linear-gradient(90deg,var(--blue),var(--green))}

/* testimonials */
.testi-band{left:0;top:2410px;width:1200px;height:555px}
.testi-head{top:2545px;color:var(--white)}
.testi-head .eyebrow{color:var(--white)}
.testi-head .heading{color:var(--white);font-size:38px;margin:6px 0 12px}
.testi-head .rule span{background:var(--white)}
.testi-head .rule span+span{background:var(--green)}
.quote-mark{left:300px;top:2610px;font-family:"Roboto",sans-serif;font-weight:700;font-size:130px;line-height:1;color:var(--green)}
.quote-text{left:320px;top:2665px;width:560px;text-align:center;color:var(--white);font-style:italic;font-size:13px;line-height:24px}
.avatar{border-radius:50%;border:3px solid var(--white);background:linear-gradient(160deg,#d8c3b0,#a88368)}
.author{left:518px;top:2768px;display:flex;align-items:center;gap:10px;color:var(--white)}
.author b{font-size:15px;font-weight:600;display:block}
.author span{font-size:13px}

/* contact */
.contact-head{top:3035px}
.contact-head .heading{font-size:38px;margin:6px 0 12px}
.contact-card{top:3148px;width:284px;height:284px;border-radius:50%;background:var(--white);box-shadow:0 12px 40px rgba(0,0,0,.08);text-align:center}
.contact-card .icon{width:78px;height:78px;border-radius:50%;background:var(--green);margin:56px auto 0;display:flex;align-items:center;justify-content:center}
.contact-card h3{font-size:21px;font-weight:500;color:#333;margin-top:20px}
.contact-card p{font-size:12.4px;line-height:24px;color:var(--muted);margin-top:6px;padding:0 56px}

/* footer */
.footer-band{left:0;top:3495px;width:1200px;height:360px}
.footer-brand{left:170px;top:3660px;width:180px;font-size:30px;color:var(--white)}
.footer-brand small{display:block;font-size:17px;letter-spacing:4px;margin-top:6px;font-weight:600}
.footer-nav{left:459px;top:3657px;display:flex;align-items:center;font-size:11.5px;color:var(--white);letter-spacing:.3px}
.footer-nav .dot{width:3px;height:3px;border-radius:50%;background:var(--white);margin:4px 19px 0}
.subscribe{left:456px;top:3701px;display:flex;gap:4px}
.subscribe .field{width:373px;height:48px;border-radius:24px;background:var(--white);font-size:13px;color:#666;display:flex;align-items:center;padding-left:27px}
.subscribe .btn{width:150px;height:48px;border-radius:24px;background:var(--green);color:var(--white);font-weight:600;font-size:14px;display:flex;align-items:center;justify-content:center}
.copyright{left:0;top:3807px;width:1200px;text-align:center;font-size:12px;color:var(--white)}
.copyright u{font-weight:600}
</style>
</head>
<body>
<div class="page">

  <!-- header -->
  <div class="abs topline"></div>
  <div class="abs contact-pill">
    <div class="call">
      <svg width="11" height="11" viewBox="0 0 24 24"><path fill="#fff" d="M6.6 10.8a15.1 15.1 0 0 0 6.6 6.6l2.2-2.2a1 1 0 0 1 1-.25 11.4 11.4 0 0 0 3.6.57 1 1 0 0 1 1 1V20a1 1 0 0 1-1 1A17 17 0 0 1 3 4a1 1 0 0 1 1-1h3.5a1 1 0 0 1 1 1c0 1.25.2 2.45.57 3.57a1 1 0 0 1-.25 1z"/></svg>
      Call Us : +1 888 888 8888
    </div>
    <div class="mail">
      <svg width="12" height="10" viewBox="0 0 24 18"><path fill="#fff" d="M0 0h24v18H0z"/><path fill="none" stroke="#3f78c0" stroke-width="2" d="M1 1l11 8 11-8"/></svg>
      Mail Us : info@companyname.com
    </div>
  </div>
  <div class="abs brand header-brand">VELMIRA<small>HEALTH</small></div>
  <nav class="abs nav">
    <a class="active" href="#">Home</a><span class="dot"></span>
    <a href="#">About Us</a><span class="dot"></span>
    <a href="#">Services</a><span class="dot"></span>
    <a href="#">Patient Info</a><span class="dot"></span>
    <a href="#">Resources</a><span class="dot"></span>
    <a href="#">Contact Us</a>
  </nav>
  <div class="abs quote-btn">Get A Quote</div>

  <!-- hero -->
  <div class="abs hero-photo" role="img" aria-label="Nurse in blue scrubs preparing a patient's arm for dialysis in a bright clinic room"></div>
  <svg class="abs" style="left:0;top:600px" width="1200" height="115" viewBox="0 0 1200 115">
    <path fill="#fff" d="M0 95 C180 120 360 95 520 70 C700 40 820 20 940 30 C1060 40 1130 80 1200 110 L1200 115 L0 115Z"/>
  </svg>
  <div class="abs follow-line"></div>
  <div class="abs social" style="top:383px"><svg width="10" height="10"><circle cx="5" cy="5" r="3" fill="#3f78c0"/></svg></div>
  <div class="abs social" style="top:423px"><svg width="10" height="10"><rect x="1" y="1" width="8" height="8" rx="2" fill="none" stroke="#3f78c0" stroke-width="1.5"/></svg></div>
  <div class="abs social" style="top:464px"><svg width="10" height="10"><path d="M2 1l7 4-7 4z" fill="#3f78c0"/></svg></div>
  <div class="abs follow-text">FOLLOW US</div>
  <h1 class="abs hero-title">VELMIRA<br>HEALTH</h1>
  <div class="abs outline-btn hero-btn">GET STARTED
    <svg width="11" height="11" viewBox="0 0 12 12"><circle cx="6" cy="6" r="6" fill="#3f78c0"/><path d="M5 3.5L7.5 6 5 8.5" stroke="#fff" stroke-width="1.5" fill="none"/></svg>
  </div>
  <div class="abs dots"><span></span><span class="on"></span><span></span></div>

  <!-- about -->
  <div class="abs about-leaf" role="img" aria-label="Green-tinted clinic corridor"></div>
  <div class="abs about-ring"></div>
  <div class="abs about-photo" role="img" aria-label="Dialysis treatment room with machines by the window"></div>
  <section class="abs about-text">
    <div class="eyebrow">OUR CLINIC</div>
    <h2 class="heading about-heading" style="font-size:34px;margin:6px 0 14px">VELMIRA HEALTH</h2>
    <div class="rule"><span></span><span></span></div>
    <p>Lorem ipsum dolor sit amet, consectetur adipiscing elit, sed do eiusmod tempor incididunt ut labore et dolore magna aliqua. Ut enim ad minim veniam, quis nostrud exercitation ullamco laboris nisi ut aliquip ex ea commodo consequat. Duis aute irure dolor in reprehenderit in voluptate velit esse cillum dolore eu fugiat nulla pariatur. Excepteur sint occaecat cupidatat non proident, sunt in culpa qui officia deserunt mollit anim id est laborum. Lorem ipsum dolor sit amet, consectetur adipiscing elit, sed do eiusmod tempor incididunt ut labore et dolore magna aliqua. Ut enim ad minim veniam, quis nostrud exercitation ullamco laboris nisi ut aliquip ex ea commodo consequat. Duis aute irure dolor in reprehenderit in voluptate velit esse cillum dolore eu fugiat nulla pariatur. Excepteur sint occaecat cupidatat in culpa qui officia deserunt mollit anim id est laborum."</p>
    <div class="outline-btn learn-btn">LEARN MORE
      <svg width="11" height="11" viewBox="0 0 12 12"><circle cx="6" cy="6" r="6" fill="#3f78c0"/><path d="M5 3.5L7.5 6 5 8.5" stroke="#fff" stroke-width="1.5" fill="none"/></svg>
    </div>
  </section>

  <!-- mission -->
  <svg class="abs mission-band" viewBox="0 0 1200 420">
    <defs>
      <linearGradient id="missionGrad" x1="0" x2="1" y1="0" y2="0">
        <stop offset="0" stop-color="#3f78c0"/>
        <stop offset=".55" stop-color="#4f8a88"/>
        <stop offset="1" stop-color="#6aa23b"/>
      </linearGradient>
    </defs>
    <path fill="url(#missionGrad)" d="M0 20 C90 -5 170 0 260 40 C380 95 470 90 600 55 C720 20 820 60 930 60 C1050 60 1120 0 1200 5 L1200 410 C1100 400 1000 380 880 400 C760 420 640 370 520 360 C380 350 320 430 180 420 C100 415 50 400 0 410Z"/>
  </svg>
  <div class="abs mission-photo" role="img" aria-label="Smiling patient and doctor beside an IV stand"></div>
  <section class="abs mission-text">
    <h2>OUR MISSION</h2>
    <div class="rule"><span></span><span></span></div>
    <p>Lorem ipsum dolor sit amet, consectetur adipiscing elit, sed do eiusmod tempor incididunt ut labore et dolore magna aliqua. Ut enim ad minim veniam, quis nostrud exercitation ullamco laboris nisi ut aliquip ex ea commodo consequat. Duis aute irure dolor in reprehenderit in voluptate velit esse cillum dolore eu fugiat nulla pariatur.</p>
  </section>

  <!-- services -->
  <section class="abs center services-head">
    <div class="eyebrow">WHAT WE DO</div>
    <h2 class="heading" style="font-size:38px;margin:6px 0 12px">OUR SERVICES</h2>
    <div class="rule"><span></span><span></span></div>
  </section>
  <div class="abs service" style="left:144px">
    <div class="photo" role="img" aria-label="Doctor reviewing a hemodialysis machine with a seated patient" style="background:linear-gradient(160deg,#c9d8ea,#7d9cc4 60%,#2c3f66)"></div>
    <div class="label">HEMODIALYSIS</div>
  </div>
  <div class="abs service" style="left:459px">
    <div class="photo" role="img" aria-label="Gloved hands connecting a line to a patient's arm" style="background:linear-gradient(160deg,#a33a55,#c97a88 45%,#8fb6dc)"></div>
    <div class="label alt">PERITONEAL DIALYSIS</div>
  </div>
  <div class="abs service" style="left:775px">
    <div class="photo" role="img" aria-label="Patient resting in bed during home treatment" style="background:linear-gradient(160deg,#eef1f4,#d6dde4 60%,#b9c7d6)"></div>
    <div class="label">HOME HEMODIALYSIS</div>
  </div>

  <!-- testimonials -->
  <svg class="abs testi-band" viewBox="0 0 1200 555">
    <path fill="#3f78c0" d="M0 25 C100 0 200 -5 320 25 C430 55 520 70 640 40 C760 10 850 -5 960 35 C1060 70 1140 50 1200 30 L1200 540 C1100 560 980 555 860 520 C740 490 640 500 520 530 C380 565 260 540 150 520 C90 510 40 520 0 525Z"/>
  </svg>
  <section class="abs center testi-head">
    <div class="eyebrow">REVIEWS</div>
    <h2 class="heading" style="font-size:38px;margin:6px 0 12px;color:#fff">TESTIMONIALS</h2>
    <div class="rule"><span></span><span></span></div>
  </section>
  <div class="abs avatar" role="img" aria-label="Reviewer portrait" style="left:131px;top:2527px;width:138px;height:138px"></div>
  <div class="abs avatar" role="img" aria-label="Reviewer portrait" style="left:886px;top:2537px;width:78px;height:78px"></div>
  <div class="abs avatar" role="img" aria-label="Reviewer portrait" style="left:91px;top:2756px;width:78px;height:78px"></div>
  <div class="abs avatar" role="img" aria-label="Reviewer portrait" style="left:950px;top:2718px;width:138px;height:138px;background:linear-gradient(160deg,#e9eef0,#b9a08a)"></div>
  <div class="abs quote-mark">&ldquo;</div>
  <p class="abs quote-text">"Lorem ipsum dolor sit amet, consectetur adipiscing elit, sed do eiusmod tempor incididunt ut labore et dolore magna aliqua. Ut enim ad minim veniam, quis nostrud exercitation ullamco laboris nisi ut aliquip ex ea commodo consequat. Lorem ipsum dolor sit amet, consectetur eiusmod tempor incididunt ut labore et dolore magna aliqua."</p>
  <div class="abs author">
    <div class="avatar" role="img" aria-label="Reviewer portrait" style="width:66px;height:66px;border-color:#6aa23b"></div>
    <div><b>- John Doe</b><span>Company name</span></div>
  </div>

  <!-- contact -->
  <section class="abs center contact-head">
    <div class="eyebrow">GET IN TOUCH</div>
    <h2 class="heading" style="font-size:38px;margin:6px 0 12px">CONTACT US</h2>
    <div class="rule"><span></span><span></span></div>
  </section>
  <div class="abs contact-card" style="left:139px">
    <div class="icon"><svg width="16" height="20" viewBox="0 0 16 20"><path fill="#fff" d="M8 0a8 8 0 0 0-8 8c0 6 8 12 8 12s8-6 8-12a8 8 0 0 0-8-8zm0 11a3 3 0 1 1 0-6 3 3 0 0 1 0 6z"/></svg></div>
    <h3>Address:</h3>
    <p>123, Lorem ipsum dolor sit amet, consect</p>
  </div>
  <div class="abs contact-card" style="left:458px">
    <div class="icon"><svg width="18" height="14" viewBox="0 0 24 18"><path fill="#fff" d="M0 0h24v18H0z"/><path fill="none" stroke="#6aa23b" stroke-width="2" d="M1 1l11 8 11-8"/></svg></div>
    <h3>Email:</h3>
    <p>info@companyname.com</p>
  </div>
  <div class="abs contact-card" style="left:774px">
    <div class="icon"><svg width="16" height="16" viewBox="0 0 24 24"><path fill="#fff" d="M6.6 10.8a15.1 15.1 0 0 0 6.6 6.6l2.2-2.2a1 1 0 0 1 1-.25 11.4 11.4 0 0 0 3.6.57 1 1 0 0 1 1 1V20a1 1 0 0 1-1 1A17 17 0 0 1 3 4a1 1 0 0 1 1-1h3.5a1 1 0 0 1 1 1c0 1.25.2 2.45.57 3.57a1 1 0 0 1-.25 1z"/></svg></div>
    <h3>Phone:</h3>
    <p>+1 888 888 8888</p>
  </div>

  <!-- footer -->
  <svg class="abs footer-band" viewBox="0 0 1200 360">
    <path fill="#3f78c0" d="M0 15 C120 -5 240 0 360 35 C470 65 560 75 660 45 C770 10 860 0 960 30 C1060 60 1140 40 1200 20 L1200 360 L0 360Z"/>
  </svg>
  <div class="abs brand footer-brand">VELMIRA<small>HEALTH</small></div>
  <nav class="abs footer-nav">
    <span>HOME</span><span class="dot"></span>
    <span>ABOUT US</span><span class="dot"></span>
    <span>SERVICES</span><span class="dot"></span>
    <span>PATIENT INFO</span><span class="dot"></span>
    <span>RESOURCES</span><span class="dot"></span>
    <span>CONTACT US</span>
  </nav>
  <div class="abs subscribe">
    <div class="field">Email address</div>
    <div class="btn">SUBSCRIBE</div>
  </div>
  <p class="abs copyright">© 2024 <u>Velmira Health</u> — All Rights Reserved.</p>

</div>
</body>
</html>
```